NEW Wordpress Website Design for a Dynamic Long Term Healthcare Company in Hawaii

I would like a new website design for my current company, Marlow Health Collective, which has two different brands - Marlow Homecare and Marlow Senior Living. You can see the current website at www.marlowhealth-example.com. The website should be built using Wordpress Software and the Framewise theme. The website should have a local Hawaii island/tropical feel, but look professional for healthcare. I'm looking for something fresh, and want the designer to select colors, styles, etc.

In the Header, on all pages, I would like a menu that includes Home Care, Senior Living, Rates, and About Us.
Under each of the Header Menu Titles, I would like these drop downs included:
Home Care (drop down pages)- Nurse Aide Care, 24-Hour Home Care, Skilled Nursing, Lifestyle Aide, Hospice at Home, Bathing & Meal Service.
Senior Living (drop down pages) - Long-Term Stay, Short-Term Stay.
Rates (drop down page) - Rates.
About Us (drop down pages) - Our Mission, Ohana Talk, About Dana Marlow.

In the footer, on all pages, you should include the address: 248 Pueo Lane, Suite 310, Honolulu, HI 96817. Phone number: 808-555-0172
The footer should also include buttons for a page called Learn, Caregiver Jobs, and each of the service page links to include: Nurse Aide Care, 24-Hour Home Care, Skilled Nursing, Lifestyle Aide, Hospice at Home, Bathing & Meal Service.
Please don't take the current website and redesign a few aspects. I'm looking for a completely different look and feel.

Target Market(s)

40-80 year olds

Industry/Entity Type

Long Term Healthcare

Coding

Coded - Design and coding required

Requirements
Should not have
• Our existing website as a template. We are looking for a complete redesign. Thank you.

```html
<!DOCTYPE html>
<html lang="en">
<head>
<meta charset="utf-8">
<title>Marlow Health Collective</title>
<link href="https://fonts.googleapis.com/css2?family=Gelasio:ital,wght@0,500;0,600;1,400&family=Poppins:ital,wght@0,400;0,500;0,600;1,400&display=swap" rel="stylesheet">
<style>
:root{
  --teal:#2c5e7b;
  --teal-dark:#234d66;
  --teal-light:#e9f0f4;
  --ink:#1f2a33;
  --muted:#6b7680;
  --line:#e4e8eb;
  --white:#ffffff;
  --paper:#ffffff;
}
*{box-sizing:border-box;margin:0;padding:0}
html,body{width:1200px;height:5286px;overflow:hidden}
body{position:relative;background:var(--paper);font-family:"Poppins",sans-serif;color:var(--ink)}
.abs{position:absolute}
.serif{font-family:"Gelasio",serif}
.btn{position:absolute;display:flex;align-items:center;justify-content:center;background:var(--teal);color:var(--white);font-size:12px;border-radius:18px}
.label{position:absolute;color:var(--teal);font-size:13px}
.bar-heading{position:absolute;border-left:3px solid var(--teal);padding-left:10px;font-family:"Gelasio",serif;font-weight:600;color:var(--ink)}
.body-text{position:absolute;font-size:11.5px;line-height:18.5px;color:var(--ink)}
.ph{position:absolute}

/* top bar & nav */
.topbar{top:0;left:0;width:1200px;height:29px;background:var(--teal-dark);color:var(--white);font-size:9px;display:flex;align-items:center;padding-left:100px;gap:18px}
.nav{top:29px;left:0;width:1200px;height:76px;background:var(--white)}
.brand{position:absolute;left:100px;top:24px;display:flex;align-items:center;gap:8px;font-family:"Gelasio",serif;font-weight:600;font-size:14px;color:var(--ink)}
.brand-dot{width:26px;height:26px;border-radius:50%;background:var(--teal)}
.menu{position:absolute;left:194px;top:32px;display:flex;gap:26px;font-size:9.5px;color:var(--muted);letter-spacing:.3px}
.menu .on{color:var(--teal);font-weight:500}
.socials{position:absolute;left:915px;top:26px;display:flex;gap:8px}
.socials span{width:24px;height:24px;border-radius:50%;background:var(--teal-dark)}
.contact-top{position:absolute;left:1030px;top:24px;border-left:1px solid var(--line);padding-left:12px;font-size:8.5px;color:var(--muted);line-height:14px}
.contact-top b{color:var(--ink);font-weight:600}

/* hero */
.hero{top:106px;left:0;width:1200px;height:586px;background:linear-gradient(100deg,#2f4a26 0%,#4d6b35 40%,#6f8a54 70%,#8ea27a 100%)}
.hero-title{position:absolute;left:109px;top:172px;font-family:"Gelasio",serif;font-weight:600;font-size:39px;line-height:55px;color:var(--white)}
.hero-text{position:absolute;left:109px;top:290px;width:520px;font-size:11.5px;line-height:18.5px;color:var(--white)}

/* services cards */
.svc-card{position:absolute;top:1438px;width:489px;height:310px;overflow:hidden}
.svc-card .ph{left:0;top:0;width:100%;height:256px}
.svc-card .cap{position:absolute;left:0;bottom:0;width:100%;height:54px;background:var(--teal);color:var(--white);display:flex;align-items:center;justify-content:center;font-family:"Gelasio",serif;font-weight:600;font-size:17px;letter-spacing:.5px}

/* home care grid */
.box{position:absolute;width:302px;height:316px;border:1px solid var(--line);background:var(--white)}
.box .tag{position:absolute;right:0;top:37px;width:92px;height:24px;border:1px solid var(--line);border-right:none;font-size:10.5px;color:var(--muted);display:flex;align-items:center;justify-content:center}
.box .icon{position:absolute;left:37px;top:37px;width:68px;height:68px;border-radius:50%;background:var(--teal)}
.box h3{position:absolute;left:37px;top:120px;font-size:17px;font-weight:600;letter-spacing:-.3px}
.box p{position:absolute;left:37px;top:166px;width:200px;font-size:9.5px;line-height:15px;color:var(--muted)}
.box svg{position:absolute;left:37px;top:250px}

/* senior living */
.ticks{position:absolute;left:638px;top:3380px;font-size:10.5px;line-height:28px}
.ticks div{display:flex;align-items:center;gap:10px}

/* testimonial */
.testi{top:3566px;left:0;width:1200px;height:507px;background:linear-gradient(120deg,#1e3440 0%,#2f4c57 50%,#3d5b61 100%)}
.testi h2{position:absolute;left:0;top:88px;width:100%;text-align:center;font-family:"Gelasio",serif;font-weight:600;font-size:27px;color:var(--white)}
.testi blockquote{position:absolute;left:185px;top:186px;width:830px;text-align:center;font-style:italic;font-size:14.5px;line-height:23px;color:var(--white)}

/* CTA */
.cta{top:4153px;left:0;width:1200px;height:454px;background:linear-gradient(90deg,#5a4636 0%,#8a7a3f 35%,#b2b55a 65%,#8fa3a0 100%)}
.cta h2{position:absolute;left:0;top:130px;width:100%;text-align:center;font-family:"Gelasio",serif;font-weight:600;font-size:39px;line-height:50px;color:var(--white)}
.contact-bar{top:4549px;left:55px;width:1088px;height:175px;background:var(--teal)}
.cb-item{position:absolute;top:58px;display:flex;align-items:center;gap:22px;color:var(--white)}
.cb-item .ring{width:58px;height:58px;border-radius:50%;background:var(--white);display:flex;align-items:center;justify-content:center}
.cb-item .t{font-family:"Gelasio",serif;font-size:17px}
.cb-item .n{font-size:15px;letter-spacing:4px;margin-top:4px}

/* footer */
.footer{top:4849px;left:0;width:1200px;height:437px;background:var(--teal-dark);color:var(--white)}
.f-brand{position:absolute;left:58px;top:60px;display:flex;align-items:center;gap:8px;font-family:"Gelasio",serif;font-weight:600;font-size:14px}
.f-brand span{width:40px;height:40px;border-radius:50%;background:var(--white)}
.f-info{position:absolute;left:58px;top:126px;font-size:8.5px;line-height:14px}
.f-social{position:absolute;left:58px;top:208px;display:flex;gap:9px}
.f-social span{width:10px;height:10px;border-radius:50%;background:var(--white)}
.f-col{position:absolute;top:73px}
.f-col h4{font-family:"Gelasio",serif;font-weight:500;font-size:17px;margin-bottom:18px}
.f-col li{list-style:none;font-size:10.5px;line-height:27.7px;display:flex;align-items:center;gap:10px}
.f-map{position:absolute;left:888px;top:117px;width:249px;height:144px;background:linear-gradient(135deg,#dfe8ef,#c7d7e3);border:3px solid var(--white)}
.f-bottom{position:absolute;left:58px;top:388px;width:1084px;border-top:1px solid rgba(255,255,255,.15);padding-top:8px;display:flex;justify-content:space-between;font-size:8px;color:rgba(255,255,255,.6)}
</style>
</head>
<body>

<div class="abs topbar"><span>Opening Hours 8:00 - 19:00</span><span>Get Help 808-555-0172</span></div>

<header class="abs nav">
  <div class="brand"><span class="brand-dot"></span>Marlow</div>
  <nav class="menu"><span class="on">HOME</span><span>ABOUT</span><span>SERVICES ▾</span><span>CONTACT US</span></nav>
  <div class="socials"><span></span><span></span><span></span></div>
  <div class="contact-top">CONTACT US<br><b>808-555-0172</b></div>
</header>

<section class="abs hero" role="img" aria-label="Nurse helping a smiling senior woman walk among tropical palms">
  <h1 class="hero-title">Compassionate Senior Care<br>With A Hawaiian Spirit</h1>
  <p class="hero-text">At Marlow Health Collective, We Offer Personalized Home Care And Senior Living Services, Blending Professional Healthcare With The Warmth And Spirit Of Hawaii To Ensure The Best For Your Loved Ones.</p>
  <div class="btn" style="left:100px;top:384px;width:135px;height:31px">Learn More</div>
</section>

<!-- About -->
<div class="label" style="left:100px;top:784px">About Us</div>
<h2 class="bar-heading" style="left:100px;top:808px;font-size:27px;line-height:50px">Our Mission</h2>
<p class="body-text" style="left:110px;top:868px;width:430px">At Marlow Health Collective, Our Mission Is To Provide Exceptional, Personalized Care To Our Clients And Their Families. With A Deep Respect For The Unique Culture Of Hawaii, We Deliver Professional, Compassionate Services That Allow Seniors To Age With Dignity And Grace. Our Commitment Is To Ensure Your Loved Ones Receive The Best Care Possible, Just Like Family.</p>
<h2 class="bar-heading" style="left:100px;top:1008px;font-size:27px;line-height:50px">About Dana Marlow</h2>
<p class="body-text" style="left:110px;top:1066px;width:430px">Dana Marlow Founded Marlow Health Collective With A Vision To Create A Nurturing Environment Where Seniors And Their Families Could Find Peace Of Mind. Born And Raised In Hawaii, Dana Embodies The Spirit Of Aloha In Every Aspect Of The Company, Ensuring That Every Client Receives Compassionate, Culturally Sensitive Care Tailored To Their Needs.</p>
<div class="btn" style="left:100px;top:1204px;width:224px;height:36px">Learn More About Our Mission</div>
<div class="ph" role="img" aria-label="Caregiver and senior resident sitting together on a sofa" style="left:600px;top:780px;width:286px;height:462px;background:linear-gradient(160deg,#c8a46a,#b7c29a 50%,#5f86a8)"></div>
<div class="ph" role="img" aria-label="Portrait of the founder in a white medical coat" style="left:897px;top:858px;width:201px;height:305px;background:linear-gradient(180deg,#e6e9ec,#cfd6dc)"></div>

<!-- Services -->
<div class="label" style="left:0;width:1234px;text-align:center;top:1312px">Services</div>
<div class="abs" style="left:416px;top:1334px;width:3px;height:53px;background:var(--teal)"></div>
<h2 class="abs serif" style="left:0;width:1234px;text-align:center;top:1340px;font-size:26px;font-weight:600">Our Services</h2>
<div class="svc-card" style="left:100px">
  <div class="ph" role="img" aria-label="Caregiver assisting a senior man at home" style="background:linear-gradient(120deg,#8b6a3c,#c9c46e 55%,#e9e3b7)"></div>
  <div class="cap">Home Care</div>
</div>
<div class="svc-card" style="left:612px">
  <div class="ph" role="img" aria-label="Caregiver and resident sharing a moment in a living room" style="background:linear-gradient(120deg,#b48f5a,#c8c38f 50%,#7fa0b8)"></div>
  <div class="cap">Senior Living</div>
</div>

<!-- Home care -->
<div class="label" style="left:0;width:1200px;text-align:center;top:1858px">Home Care</div>
<div class="abs" style="left:258px;top:1877px;width:3px;height:56px;background:var(--teal)"></div>
<h2 class="abs serif" style="left:0;width:1200px;text-align:center;top:1886px;font-size:27px;font-weight:600">Personalized Home Care With Heart</h2>
<p class="body-text" style="left:280px;top:1942px;width:640px;text-align:center">At Marlow Health Collective, Our Home Care Services Are Designed To Help Individuals Maintain Their Independence In The Comfort Of Their Own Homes. From Skilled Nursing To Lifestyle Assistance, We Create Customized Care Plans That Ensure Every Client's Unique Needs Are Met.</p>
<div class="ph" role="img" aria-label="Caregiver helping a senior man sit on his bed" style="left:100px;top:2025px;width:1000px;height:355px;background:linear-gradient(110deg,#6e5434 0%,#b8a05a 35%,#d8d688 60%,#e8e5c7 100%)"></div>

<div class="box" style="left:123px;top:2401px"><span class="tag">Service 01</span><span class="icon"></span><h3>Nurse Aide Care</h3><p>Trained aides assist with daily tasks like medication, mobility, and personal care, ensuring comfort and dignity.</p><svg width="30" height="14" viewBox="0 0 30 14"><path d="M0 7H27M21 1l6 6-6 6" fill="none" stroke="#9aa3aa" stroke-width="1.5"/></svg></div>
<div class="box" style="left:449px;top:2401px"><span class="tag">Service 02</span><span class="icon"></span><h3>24-Hour Home Care</h3><p>Round-the-clock support to meet the needs of your loved ones at any time, day or night.</p><svg width="30" height="14" viewBox="0 0 30 14"><path d="M0 7H27M21 1l6 6-6 6" fill="none" stroke="#9aa3aa" stroke-width="1.5"/></svg></div>
<div class="box" style="left:774px;top:2401px"><span class="tag">Service 03</span><span class="icon"></span><h3>Skilled Nursing</h3><p>Licensed nurses provide medical care at home, from post-op to chronic condition management.</p><svg width="30" height="14" viewBox="0 0 30 14"><path d="M0 7H27M21 1l6 6-6 6" fill="none" stroke="#9aa3aa" stroke-width="1.5"/></svg></div>
<div class="box" style="left:123px;top:2743px"><span class="tag">Service 04</span><span class="icon"></span><h3>Lifestyle Aide</h3><p>Assistance with social activities, errands, and recreation to help seniors stay engaged and active.</p><svg width="30" height="14" viewBox="0 0 30 14"><path d="M0 7H27M21 1l6 6-6 6" fill="none" stroke="#9aa3aa" stroke-width="1.5"/></svg></div>
<div class="box" style="left:449px;top:2743px"><span class="tag">Service 05</span><span class="icon"></span><h3>Hospice at Home</h3><p>Compassionate end-of-life care, ensuring comfort and peace for patients and their families.</p><svg width="30" height="14" viewBox="0 0 30 14"><path d="M0 7H27M21 1l6 6-6 6" fill="none" stroke="#9aa3aa" stroke-width="1.5"/></svg></div>
<div class="box" style="left:774px;top:2743px"><span class="tag">Service 06</span><span class="icon"></span><h3>Bathing &amp; Meal Service</h3><p>Personalized bathing assistance and meal preparation to promote hygiene and nutrition.</p><svg width="30" height="14" viewBox="0 0 30 14"><path d="M0 7H27M21 1l6 6-6 6" fill="none" stroke="#9aa3aa" stroke-width="1.5"/></svg></div>

<!-- Senior living -->
<div class="ph" role="img" aria-label="Three senior women knitting together on a sofa" style="left:100px;top:3133px;width:499px;height:355px;background:linear-gradient(110deg,#8f6a4a,#c79a6c 40%,#d9c87a 70%,#9cb5b8)"></div>
<div class="label" style="left:630px;top:3138px;font-size:12.5px">Senior Living</div>
<h2 class="bar-heading" style="left:630px;top:3166px;font-size:29px;line-height:42px">Comfortable, Safe Senior Living<br>In Paradise</h2>
<p class="body-text" style="left:640px;top:3278px;width:430px;font-size:11px;line-height:17.5px">Marlow Senior Living Offers Both Long-Term And Short-Term Stays In A Warm, Supportive Environment. Our Facilities Are Designed To Provide High-Quality Care With A Focus On Enhancing Well-Being, While Residents Enjoy The Beauty And Serenity Of Hawaii's Natural Surroundings.</p>
<div class="ticks">
  <div><svg width="16" height="16" viewBox="0 0 16 16"><rect x="1" y="1" width="14" height="14" rx="3" fill="none" stroke="#2c5e7b" stroke-width="1.3"/><path d="M4 8l3 3 5-6" fill="none" stroke="#2c5e7b" stroke-width="1.5"/></svg>Long-Term Stay</div>
  <div><svg width="16" height="16" viewBox="0 0 16 16"><rect x="1" y="1" width="14" height="14" rx="3" fill="none" stroke="#2c5e7b" stroke-width="1.3"/><path d="M4 8l3 3 5-6" fill="none" stroke="#2c5e7b" stroke-width="1.5"/></svg>Short-Term Stay</div>
</div>
<div class="btn" style="left:630px;top:3453px;width:162px;height:33px">Learn More</div>

<!-- Testimonial -->
<section class="abs testi" role="img" aria-label="Dimmed background of caregivers with seniors">
  <h2>What Our Families Say</h2>
  <blockquote>After my mom's surgery, we needed a place where she could recover with the right level of support, but we also wanted to ensure she felt at home. Marlow Senior Living provided that perfect balance. The staff treated my mom with such dignity and respect, always checking in on her well-being and encouraging her to stay active. The environment was warm and welcoming, with a tropical island feel that immediately put her at ease. I'm grateful for the incredible care she received and for the peace of mind it gave me, knowing she was in great hands."</blockquote>
  <div class="abs" style="left:538px;top:364px;width:47px;height:47px;border-radius:50%;background:#c9cfd3;border:2px solid var(--white)"></div>
  <div class="abs serif" style="left:598px;top:377px;color:var(--white);font-size:15px">– Kai R.</div>
  <div class="abs" style="left:583px;top:453px;width:6px;height:6px;border-radius:50%;background:var(--white)"></div>
</section>

<!-- CTA -->
<section class="abs cta" role="img" aria-label="Caregiver tending to a senior man in a bright bedroom">
  <h2>Competent Medical<br>Senior Care</h2>
  <div class="btn" style="left:521px;top:242px;width:156px;height:52px;border-radius:26px;font-size:11px">CONTACT US</div>
</section>
<div class="abs contact-bar">
  <div class="cb-item" style="left:35px">
    <div class="ring"><svg width="24" height="24" viewBox="0 0 24 24"><path d="M6 3l3 0 2 5-2 1.5a11 11 0 0 0 5.5 5.5L16 13l5 2v3a2 2 0 0 1-2 2A16 16 0 0 1 4 5a2 2 0 0 1 2-2z" fill="none" stroke="#2c5e7b" stroke-width="1.6"/></svg></div>
    <div><div class="t">Health Care Center</div><div class="n">808-555-0172</div></div>
  </div>
  <div class="cb-item" style="left:556px">
    <div class="ring"><svg width="24" height="24" viewBox="0 0 24 24"><path d="M6 3l3 0 2 5-2 1.5a11 11 0 0 0 5.5 5.5L16 13l5 2v3a2 2 0 0 1-2 2A16 16 0 0 1 4 5a2 2 0 0 1 2-2z" fill="none" stroke="#2c5e7b" stroke-width="1.6"/></svg></div>
    <div><div class="t">Schedule a Tour</div><div class="n">808-555-0172</div></div>
  </div>
</div>

<!-- Footer -->
<footer class="abs footer">
  <div class="f-brand"><span></span>Marlow</div>
  <div class="f-info"><b style="font-size:9.5px">Marlow Health Collective</b><br>248 Pueo Lane, Suite 310,<br>Honolulu, HI 96817<br><b>Phone:</b> 808-555-0172<br><b>Email:</b> info@marlowhealth-example.com</div>
  <div class="f-social"><span></span><span></span><span></span></div>
  <div class="f-col" style="left:334px"><h4>Quick Links</h4><ul>
    <li><svg width="10" height="8"><path d="M1 4l3 3 5-6" fill="none" stroke="#fff" stroke-width="1.4"/></svg>Learn</li>
    <li><svg width="10" height="8"><path d="M1 4l3 3 5-6" fill="none" stroke="#fff" stroke-width="1.4"/></svg>Caregiver Jobs</li>
    <li><svg width="10" height="8"><path d="M1 4l3 3 5-6" fill="none" stroke="#fff" stroke-width="1.4"/></svg>Nurse Aide Care</li>
    <li><svg width="10" height="8"><path d="M1 4l3 3 5-6" fill="none" stroke="#fff" stroke-width="1.4"/></svg>24-Hour Home Care</li>
    <li><svg width="10" height="8"><path d="M1 4l3 3 5-6" fill="none" stroke="#fff" stroke-width="1.4"/></svg>Skilled Nursing</li>
    <li><svg width="10" height="8"><path d="M1 4l3 3 5-6" fill="none" stroke="#fff" stroke-width="1.4"/></svg>Lifestyle Aide</li>
    <li><svg width="10" height="8"><path d="M1 4l3 3 5-6" fill="none" stroke="#fff" stroke-width="1.4"/></svg>Hospice at Home</li>
    <li><svg width="10" height="8"><path d="M1 4l3 3 5-6" fill="none" stroke="#fff" stroke-width="1.4"/></svg>Bathing &amp; Meal Service</li>
  </ul></div>
  <div class="f-col" style="left:611px"><h4>Our Services</h4><ul>
    <li><svg width="10" height="8"><path d="M1 4l3 3 5-6" fill="none" stroke="#fff" stroke-width="1.4"/></svg>Home Care Services</li>
    <li><svg width="10" height="8"><path d="M1 4l3 3 5-6" fill="none" stroke="#fff" stroke-width="1.4"/></svg>Senior Living Services</li>
  </ul></div>
  <div class="f-col" style="left:888px"><h4>Our Hospices</h4></div>
  <div class="f-map" role="img" aria-label="Map showing care locations across Honolulu"></div>
  <div class="f-bottom"><span>© 2024 Marlow Health Collective. All Rights Reserved</span><span>About us &nbsp;|&nbsp; Contact &nbsp;|&nbsp; Services</span></div>
</footer>

</body>
</html>
```